Realtor branding business card

modern, simple and self branding. Broker office logo needs to be used but not emphasized. Looking to brand myself

Target Market(s)

buyers, sellers and investors

Industry/Entity Type

Realtor

Contact Information for Business Card

Sample of my current business card on file

Requirements
Must have
• my website - tobiasmerrowkl.com
• Realtor logo
• Fair housing logo
Nice to have
• Colors from office logo but not a must
Should not have
• Do not want headshot

```html
<!DOCTYPE html>
<html lang="en">
<head>
<meta charset="utf-8">
<title>Brightway Realty Group – Business Card</title>
<link href="https://fonts.googleapis.com/css2?family=Montserrat:wght@400;500;700;800&display=swap" rel="stylesheet">
<style>
  :root {
    --navy: #2d2a7a;
    --navy-deep: #27246b;
    --red: #e0262b;
    --ink-grey: #6b6b75;
    --paper: #ffffff;
    --backdrop: #e9e8ec;
  }
  * { margin: 0; padding: 0; box-sizing: border-box; }
  html, body { width: 1200px; height: 930px; overflow: hidden; }
  body {
    background: var(--backdrop);
    font-family: "Montserrat", sans-serif;
    position: relative;
  }
  .card {
    position: absolute;
    width: 640px;
    height: 366px;
    border-radius: 2px;
    box-shadow: 0 10px 28px rgba(0,0,0,.18);
    overflow: hidden;
  }
  /* Back side */
  .card-back {
    left: 60px; top: 70px;
    background: linear-gradient(120deg, var(--navy-deep), var(--navy) 55%, #3a3690);
    color: var(--paper);
  }
  .card-back .brand {
    position: absolute;
    left: 0; right: 0; top: 120px;
    display: flex; align-items: center; justify-content: center; gap: 14px;
  }
  .brand-mark { width: 20px; height: 20px; background: var(--red); }
  .card-back .brand-name {
    font-weight: 800; font-size: 40px; line-height: 1; letter-spacing: -0.5px;
    color: var(--paper);
  }
  .card-back .website {
    position: absolute; left: 0; right: 0; bottom: 52px;
    text-align: center; font-size: 17px; font-weight: 500;
  }
  .website .domain { color: var(--red); }

  /* Front side */
  .card-front {
    left: 500px; top: 490px;
    background: var(--paper);
  }
  .card-front .brand {
    position: absolute; right: 40px; top: 52px;
    display: flex; align-items: center; gap: 12px;
  }
  .card-front .brand-name {
    font-weight: 800; font-size: 34px; line-height: 1; letter-spacing: -0.5px;
    color: var(--navy);
  }
  .rule { position: absolute; height: 2px; background: var(--red); }
  .rule-brand { right: 40px; top: 112px; width: 390px; }
  .agent { position: absolute; left: 40px; top: 168px; }
  .agent-name {
    font-weight: 700; font-size: 24px; color: var(--navy); letter-spacing: 0.2px;
  }
  .agent-title { font-size: 15px; color: var(--ink-grey); margin-top: 2px; }
  .rule-agent { left: 40px; top: 232px; width: 300px; }
  .contacts {
    position: absolute; left: 40px; top: 246px;
    list-style: none; font-size: 15px; color: var(--ink-grey); line-height: 23px;
  }
  .contacts li { display: flex; align-items: center; gap: 10px; }
  .contacts svg { width: 13px; height: 13px; flex: none; }
  .address {
    position: absolute; left: 40px; top: 322px;
    font-style: normal; font-size: 15px; color: var(--ink-grey); line-height: 20px;
  }
  .card-front .website {
    position: absolute; right: 40px; top: 262px;
    font-size: 16px; font-weight: 500; color: var(--navy);
  }
  .accent-bar {
    position: absolute; right: 24px; bottom: 62px;
    width: 220px; height: 16px; background: var(--red);
  }
</style>
</head>
<body>

<section class="card card-back" aria-label="Card back">
  <div class="brand">
    <span class="brand-mark"></span>
    <span class="brand-name">Brightway Realty Group</span>
  </div>
  <p class="website">www.<span class="domain">tobiasmerrowkl</span>.com</p>
</section>

<section class="card card-front" aria-label="Card front">
  <div class="brand">
    <span class="brand-mark"></span>
    <span class="brand-name">Brightway Realty Group</span>
  </div>
  <div class="rule rule-brand"></div>

  <div class="agent">
    <h1 class="agent-name">TOBIAS MERROW</h1>
    <p class="agent-title">Realtor</p>
  </div>
  <div class="rule rule-agent"></div>

  <ul class="contacts">
    <li>
      <svg viewBox="0 0 14 14" aria-hidden="true"><rect x="3.5" y="1" width="7" height="12" rx="1.5" fill="none" stroke="#2d2a7a" stroke-width="1.6"/><circle cx="7" cy="10.5" r="0.9" fill="#2d2a7a"/></svg>
      407.555.0148
    </li>
    <li>
      <svg viewBox="0 0 14 14" aria-hidden="true"><path d="M3 1.5l2.3 0.4 0.8 2.8-1.4 1.2c0.8 1.7 1.9 2.8 3.5 3.5l1.2-1.4 2.8 0.8 0.4 2.3c-0.4 0.9-1.3 1.4-2.3 1.3C5.5 11.9 2.1 8.5 1.6 3.8 1.5 2.8 2.1 1.9 3 1.5z" fill="#2d2a7a"/></svg>
      407.555.0192
    </li>
    <li>
      <svg viewBox="0 0 14 14" aria-hidden="true"><rect x="1" y="3" width="12" height="8.5" rx="1" fill="none" stroke="#2d2a7a" stroke-width="1.5"/><path d="M1.5 3.6L7 8l5.5-4.4" fill="none" stroke="#2d2a7a" stroke-width="1.5"/></svg>
      info@tobiasmerrowkl.com
    </li>
  </ul>

  <address class="address">
    418 Larkspur Avenue<br>
    Maple Springs, FL 32790
  </address>

  <p class="website">www.tobiasmerrowkl.com</p>
  <div class="accent-bar"></div>
</section>

</body>
</html>
```